Quill Harbor (IT/Network Services)

Quill Harbor, LLC provides technology services to small and medium businesses. Essentially, anytime you've every thought your business might need an "IT guy" to handle something you could instead call us to handle it. Basically, you can outsource your IT needs to us.

This is a brand new company and so we'll need a brand new website. I'd like to use WordPress to handle the site since that will make things easier for me to maintain in the long run.

The site should include a, more-or-less, static front page with the dynamic data occurring on pages linked from a navigational area.

I have a logo already designed that I would like to see used in the design. The one with "white" in the title is the official logo, just added some other versions for your perusal.

Color queues from the logo but feel free to add other colors where applicable.

The site should feel somewhat corporate but with a "younger" slant (something a 25-35 year old would enjoy).

Pages (either to be added initially or by me after design completion):
"About" section - includes company history, business philosophy, etc.
"Services" section - service options, service approach, service specifics
"Testimonials" section - (eventually)
"News" section - (eventually) industry news, company news, events, blog
Contact Links

Websites to view:
The two largest local competitors:
http://www.brightmarsh-tech.example/
http://www.kelvarworks.example/
Other local competitors:
http://www.tpbllc.example/
http://www.morrowfield.example/

Other info you might find useful:
Domain: qhllc.example
Address:
417 Elm Row S
Suite 512B
Nashville, TN 37288
Phone: 615-555-0187
Emails available for use/display:
info@qhllc.example
sales@qhllc.example

Target Market(s)

Our target clients are mainly small businesses (25 or less computer users) which means we're looking at a lot of start-ups or younger companies. We'll be interacting with many entrepreneurs and young business owners.

Requirements
Must have
• Need full WP theme (not a mockup)

```html
<!DOCTYPE html>
<html lang="en">
<head>
<meta charset="utf-8">
<title>Quill Harbor</title>
<link rel="stylesheet" href="https://fonts.googleapis.com/css2?family=Ubuntu:wght@400;500&family=Arimo:wght@400;700&display=swap">
<style>
:root{
  --orange:#e8890c;
  --dark:#2e2e30;
  --tile:#353537;
  --bg:#ececf0;
  --page:#ffffff;
  --text:#333333;
  --muted:#555555;
  --rule:#d6d6d6;
  --footer:#d3d3d6;
  --btn:#d9d9db;
  --red:#e8262f;
}
*{box-sizing:border-box;margin:0;padding:0}
html,body{width:821px;height:1200px;overflow:hidden}
body{background:var(--bg);font-family:"Arimo",Arial,sans-serif;color:var(--text);position:relative}
.page{position:absolute;left:54px;top:0;width:714px;height:1200px;background:var(--page)}
.topbar{position:absolute;left:0;top:0;width:821px;height:12px;background:var(--dark)}
.abs{position:absolute}

.brand{left:67px;top:40px;display:flex;align-items:center;gap:8px}
.brand-dot{width:30px;height:30px;border-radius:50%;background:var(--orange);flex:none}
.brand-name{font-family:"Ubuntu",sans-serif;font-size:22px;font-weight:500;color:#5a5a5a;white-space:nowrap}

.userlinks{right:67px;top:39px;font-family:"Ubuntu",sans-serif;font-size:10px;font-weight:500;color:#222;word-spacing:2px}
.social-title{right:67px;top:63px;font-family:"Ubuntu",sans-serif;font-size:10px;font-weight:500;color:#222}
.social{top:77px;width:29px;height:29px;border-radius:4px}
.social.fb{left:686px;background:#3b5fa5}
.social.tw{left:722px;background:#4bb4e6}

.nav{left:66px;top:122px;width:688px;height:46px;background:var(--dark)}
.nav-home{position:absolute;left:0;top:0;width:44px;height:46px;background:var(--orange);display:flex;align-items:center;justify-content:center}
.nav-item{position:absolute;top:0;height:46px;line-height:46px;font-family:"Ubuntu",sans-serif;font-size:13px;color:var(--orange)}
.nav-sep{position:absolute;top:6px;width:1px;height:34px;background:#444}

.hero{left:66px;top:175px;width:688px;height:313px;background:radial-gradient(ellipse at 40% 35%,#d8b48c 0%,#9b6d44 40%,#3e2718 100%)}
.cap1{left:413px;top:312px;width:341px;height:32px;background:#2a2a2a;color:#fff;font-family:"Ubuntu",sans-serif;font-size:24px;text-align:right;padding-right:14px;line-height:33px}
.cap2{left:459px;top:348px;width:295px;height:31px;background:rgba(245,240,235,.9);color:var(--orange);font-family:"Ubuntu",sans-serif;font-size:24px;text-align:right;padding-right:14px;line-height:32px}
.ctl{top:458px;width:20px;height:20px;border-radius:50%;background:#e8e8e8;color:#333;font-size:11px;font-weight:700;text-align:center;line-height:19px}
.dot{top:463px;width:11px;height:11px;border-radius:50%;background:#fff}

.tile{top:492px;width:169px;height:204px;background:var(--tile);padding:19px 7px 0 9px;color:#fff}
.tile.accent{background:var(--orange)}
.tile h3{font-family:"Ubuntu",sans-serif;font-weight:500;font-size:16px;margin-bottom:14px}
.tile p{font-size:9.8px;line-height:14.6px;letter-spacing:-0.1px}
.btn{display:inline-block;background:var(--btn);color:#222;font-size:10.5px;border-radius:4px;width:75px;height:22px;line-height:22px;text-align:center}
.tile .btn{position:absolute;left:9px;top:171px}

.sec-title{top:735px;font-family:"Ubuntu",sans-serif;font-size:16px;font-weight:500;color:#1e1e1e}
.vrule{top:733px;width:1px;height:280px;background:var(--rule)}
.photo{left:67px;top:775px;width:277px;height:112px;background:linear-gradient(135deg,#e7ecec 0%,#b7c2c2 45%,#2d2f30 70%,#cdd3d3 100%)}
.welcome-lead{left:67px;top:904px;font-size:10.5px;font-weight:700;color:#111}
.welcome-body{left:67px;top:919px;width:270px;font-size:10.2px;line-height:14.6px;color:var(--muted)}

.news{left:401px;width:170px;display:flex;gap:11px}
.news-date{width:38px;height:37px;border-radius:6px;background:var(--dark);color:#fff;font-family:"Ubuntu",sans-serif;font-size:16px;text-align:center;line-height:39px;flex:none;margin-top:-4px}
.news-head{font-size:10.5px;text-decoration:underline;color:#222;display:block;margin-bottom:3px}
.news-text{font-size:9.5px;line-height:14.5px;color:#333}

.quote{left:596px;width:158px}
.quote-mark{position:absolute;left:0;top:2px;width:11px;height:11px;border-radius:50%;border:1px solid #bbb}
.quote p{margin-left:20px;font-size:10px;line-height:14.6px;color:#333}
.quote-by{display:block;text-align:right;font-size:10px;font-style:italic;color:var(--orange);margin-top:5px}

.footer{left:54px;top:1040px;width:714px;height:160px;background:var(--footer)}
.f-head{font-family:"Ubuntu",sans-serif;font-size:15px;font-weight:400;color:#111}
.f-list{list-style:none;font-size:10px;color:#333;line-height:16.5px}
.f-list li::before{content:"";display:inline-block;border-left:4px solid #444;border-top:3px solid transparent;border-bottom:3px solid transparent;margin-right:6px;vertical-align:1px}
.call{left:330px;top:1068px;font-size:15px;color:#111}
.phone-icon{left:330px;top:1100px;width:27px;height:28px;border-radius:4px;background:var(--red)}
.phone-num{left:362px;top:1103px;font-size:17.5px;color:#222}
.f-brand{left:575px;top:1094px;display:flex;align-items:center;gap:8px}
.f-brand .brand-dot{width:32px;height:32px;background:#777}
.f-brand .brand-name{font-size:24px;color:#6a6a6a}
.copy{left:87px;top:1179px;font-size:9px;color:#aaa}
</style>
</head>
<body>
<div class="page"></div>
<div class="topbar"></div>

<header>
  <div class="abs brand"><span class="brand-dot"></span><span class="brand-name">Quill Harbor</span></div>
  <div class="abs userlinks">NEW USER? &nbsp;| &nbsp;REGISTRATION &nbsp;| &nbsp;SIGN IN &nbsp;| &nbsp;HELP</div>
  <div class="abs social-title">SOCIALIZE WITH US</div>
  <span class="abs social fb" role="img" aria-label="Social profile link"></span>
  <span class="abs social tw" role="img" aria-label="Social profile link"></span>

  <nav class="abs nav">
    <span class="nav-home">
      <svg width="18" height="17" viewBox="0 0 18 17" fill="none" stroke="#fff" stroke-width="1.5"><path d="M1 8 9 1l8 7"/><path d="M3.5 6.5V16h11V6.5"/><path d="M7.5 16v-5h3v5"/></svg>
    </span>
    <span class="nav-item" style="left:62px">ABOUT US</span>
    <span class="nav-sep" style="left:138px"></span>
    <span class="nav-item" style="left:152px">SOLUTIONS</span>
    <span class="nav-sep" style="left:232px"></span>
    <span class="nav-item" style="left:246px">SERVICES</span>
    <span class="nav-sep" style="left:315px"></span>
    <span class="nav-item" style="left:329px">BLOG</span>
    <span class="nav-sep" style="left:376px"></span>
    <span class="nav-item" style="left:391px">RESOURCES</span>
    <span class="nav-sep" style="left:472px"></span>
    <span class="nav-item" style="left:486px">CONTACT US</span>
  </nav>
</header>

<section>
  <div class="abs hero" role="img" aria-label="Sepia-toned globe showing Africa and Europe with sweeping light streaks"></div>
  <div class="abs cap1">EXCLUSIVE PROJECTS</div>
  <div class="abs cap2">AN UNIQUE DESIGN</div>
  <span class="abs ctl" style="left:597px">&laquo;</span>
  <span class="abs dot" style="left:632px"></span>
  <span class="abs dot" style="left:653px"></span>
  <span class="abs dot" style="left:675px"></span>
  <span class="abs dot" style="left:699px"></span>
  <span class="abs ctl" style="left:726px">&raquo;</span>
</section>

<section>
  <article class="abs tile accent" style="left:66px">
    <h3>BANK SOLUTION</h3>
    <p>Mam libero tempore massasoluta nobis est eligendi omnis volusas sumenda est, omnis dolorsereele dusempquibus damet, aurerum odes necessitatibulas saepe eve niet uto luptates estu repudisndae sint et molestiae non rec lorem..</p>
    <span class="btn">Read more...</span>
  </article>
  <article class="abs tile" style="left:240px">
    <h3>HEALTH CARE</h3>
    <p>Mam libero tempore massasoluta nobis est eligendi omnis volusas sumenda est, omnis dolorsereele dusempquibus damet, aurerum odes necessitatibulas saepe eve niet uto luptates estu repudisndae sint et molestiae non rec lorem..</p>
    <span class="btn">Read more...</span>
  </article>
  <article class="abs tile" style="left:413px">
    <h3>SMALL BUSINESS</h3>
    <p>Mam libero tempore massasoluta nobis est eligendi omnis volusas sumenda est, omnis dolorsereele dusempquibus damet, aurerum odes necessitatibulas saepe eve niet uto luptates estu repudisndae sint et molestiae non rec lorem..</p>
    <span class="btn">Read more...</span>
  </article>
  <article class="abs tile" style="left:587px">
    <h3>FINANCE</h3>
    <p>Mam libero tempore massasoluta nobis est eligendi omnis volusas sumenda est, omnis dolorsereele dusempquibus damet, aurerum odes necessitatibulas saepe eve niet uto luptates estu repudisndae sint et molestiae non rec lorem..</p>
    <span class="btn">Read more...</span>
  </article>
</section>

<section>
  <h2 class="abs sec-title" style="left:67px">WELCOME TO OUR COMPANY</h2>
  <div class="abs photo" role="img" aria-label="Business team reviewing documents in a bright office"></div>
  <div class="abs welcome-lead">Est omnis dolorserelederate tenpqubismet</div>
  <p class="abs welcome-body">aurem odes necessaritybus saepae eveniet tolurppeds estomo usandaeltaque earum hic tenetrum a sapiente delectus, ut aut reiciendis voluptatibus maiores atias con sequatur aut</p>
  <span class="abs btn" style="left:72px;top:986px">Read more...</span>

  <span class="abs vrule" style="left:374px"></span>

  <h2 class="abs sec-title" style="left:403px">OUR NEWS</h2>
  <div class="abs news" style="top:780px"><span class="news-date">27</span><div><span class="news-head">January 27-2012</span><p class="news-text">Wed test lab oram euman libero tempore, set cumpol</p></div></div>
  <div class="abs news" style="top:845px"><span class="news-date">29</span><div><span class="news-head">Febduary 20-2012</span><p class="news-text">sid dolor trans orum eunam libero temporate dessolarate</p></div></div>
  <div class="abs news" style="top:909px"><span class="news-date">10</span><div><span class="news-head">April 27-2012</span><p class="news-text">Wed test lab oram euman libero tempore, set cumpol</p></div></div>
  <span class="abs btn" style="left:405px;top:986px">Read more...</span>

  <span class="abs vrule" style="left:580px"></span>

  <h2 class="abs sec-title" style="left:609px">TESTIMONIAL</h2>
  <div class="abs quote" style="top:773px"><span class="quote-mark"></span><p>Lorem Ipsum is simply dummy text of the printing and typeset-ting industry.</p><span class="quote-by">Nora Velt</span></div>
  <div class="abs quote" style="top:839px"><span class="quote-mark"></span><p>Lorem Ipsum is simply dummy text of the printing and typeset-ting industry.</p><span class="quote-by">Tessa Marlo</span></div>
  <div class="abs quote" style="top:905px"><span class="quote-mark"></span><p>Lorem Ipsum is simply dummy text of the printing and typeset-ting industry.</p><span class="quote-by">Nora Velt</span></div>
  <span class="abs btn" style="left:614px;top:986px">Read more...</span>
</section>

<footer>
  <div class="abs footer"></div>
  <div class="abs" style="left:99px;top:1066px"><h4 class="f-head">Links</h4></div>
  <ul class="abs f-list" style="left:91px;top:1095px"><li>Catalog</li><li>Solutions</li><li>Guarantee</li></ul>
  <div class="abs" style="left:215px;top:1066px"><h4 class="f-head">Join In</h4></div>
  <ul class="abs f-list" style="left:207px;top:1094px"><li>Sign Up</li><li>Forums</li><li>Promotions</li></ul>
  <div class="abs call">Call now to find out how :</div>
  <span class="abs phone-icon">
    <svg width="27" height="28" viewBox="0 0 27 28"><path d="M9 6c1.5-1 2.5 0 3 1.5l1 2.5c.4 1-.2 1.8-1 2.3l-.8.5c.8 2 2 3.4 3.8 4.6l.7-.7c.7-.7 1.6-.9 2.4-.3l2.2 1.5c1.2.8 1.4 2 .3 3L19 22c-1.5 1.2-4 .6-6.5-1.8C9.5 17.4 7.5 13.5 7.4 10.5 7.3 8.5 7.8 6.8 9 6z" fill="#fff"/></svg>
  </span>
  <div class="abs phone-num">1-800-555-0143</div>
  <div class="abs f-brand"><span class="brand-dot"></span><span class="brand-name">Quill Harbor</span></div>
  <div class="abs copy">Copyright@2012.All Rights Reserved</div>
</footer>
</body>
</html>
```